New business card/stationary for a consulting company

I am looking for a clean and very professional looking business card for my consulting company as well as corresponding stationary. I am uploading our logo. I like simple and powerful for the feel. No graphics but I am open on everything else. Below is my contact information but would like the final to be in a version I can add my employees information into and print. Thank you.

Daniel Whitcombe
dan@ferncliffadvisory.com
2870 North 9th Avenue, Summit Floor, Elm Ridge, Illinois 60531
www.ferncliffadvisory.com

Industry/Entity Type

Consulting

Contact Information for Business Card

Daniel Whitcombe
dan@ferncliffadvisory.com
www.ferncliffadvisory.com

Font styles to use
Serif
Sans Serif

Requirements
Must have
• Our logo and the business card details.
Nice to have
• our website www.ferncliffadvisory.com

```html
<!DOCTYPE html>
<html lang="en">
<head>
<meta charset="utf-8">
<title>Ferncliff Advisory — Business Card</title>
<link rel="stylesheet" href="https://fonts.googleapis.com/css2?family=Open+Sans:wght@300;400;700&family=Open+Sans+Condensed:wght@700&display=swap">
<style>
  :root {
    --backdrop: #3a322e;
    --card: #141414;
    --card-edge: #1d1d1d;
    --text: #f2f2f2;
    --muted: #9a9a9a;
    --mark: #b9b9b9;
    --rule: #cfcfcf;
  }
  * { box-sizing: border-box; margin: 0; padding: 0; }
  html, body { width: 1200px; height: 864px; overflow: hidden; }
  body {
    background: var(--backdrop);
    font-family: "Open Sans", Arial, sans-serif;
    color: var(--text);
    position: relative;
  }
  .card {
    position: absolute;
    top: 277px;
    width: 540px;
    height: 309px;
    background: var(--card);
    border: 1px solid var(--card-edge);
    box-shadow: 0 10px 28px rgba(0,0,0,.45);
  }
  .card--front { left: 40px; }
  .card--back { left: 620px; }

  /* Front */
  .front-mark {
    position: absolute;
    left: 0; right: 0; top: 104px;
    display: flex; align-items: center; justify-content: center; gap: 14px;
  }
  .front-mark__square { width: 20px; height: 20px; background: var(--mark); }
  .front-mark__name {
    font-weight: 300; font-size: 30px; letter-spacing: 3px;
    color: var(--mark); text-transform: uppercase;
  }
  .front-web {
    position: absolute; left: 0; right: 0; top: 196px;
    text-align: center; font-size: 12px; letter-spacing: 6px;
    color: var(--muted); font-weight: 300;
  }

  /* Back */
  .brand {
    position: absolute; right: 32px; top: 40px;
    display: flex; flex-direction: column; align-items: flex-end; gap: 8px;
  }
  .brand__square { width: 16px; height: 16px; background: var(--text); }
  .brand__name {
    font-weight: 300; font-size: 20px; letter-spacing: 1.5px;
    text-transform: uppercase;
  }
  .holder {
    position: absolute; left: 32px; top: 60px;
  }
  .holder__name {
    font-family: "Open Sans Condensed", "Open Sans", sans-serif;
    font-weight: 700; font-size: 18px; letter-spacing: .5px;
    text-transform: uppercase; margin-bottom: 14px;
  }
  .holder__address {
    font-style: normal; font-size: 12px; line-height: 1.35; font-weight: 400;
  }
  .divider {
    position: absolute; left: 32px; right: 32px; top: 154px;
    height: 1px; background: var(--rule);
  }
  .contact {
    position: absolute; right: 32px; bottom: 44px;
    list-style: none; text-align: right; font-size: 13px; line-height: 1.6;
  }
  .contact li { display: flex; align-items: center; justify-content: flex-end; gap: 8px; }
  .contact svg { width: 12px; height: 12px; fill: none; stroke: var(--text); stroke-width: 1.6; }
</style>
</head>
<body>
  <section class="card card--front" aria-label="Business card front">
    <div class="front-mark">
      <span class="front-mark__square"></span>
      <span class="front-mark__name">Ferncliff Advisory</span>
    </div>
    <p class="front-web">www.ferncliffadvisory.com</p>
  </section>

  <section class="card card--back" aria-label="Business card back">
    <div class="brand">
      <span class="brand__square"></span>
      <span class="brand__name">Ferncliff Advisory</span>
    </div>
    <div class="holder">
      <h1 class="holder__name">Daniel Whitcombe</h1>
      <address class="holder__address">
        2870 North 9th Avenue<br>
        Summit Floor, Elm Ridge<br>
        Illinois 60531
      </address>
    </div>
    <div class="divider"></div>
    <ul class="contact">
      <li>dan@ferncliffadvisory.com
        <svg viewBox="0 0 12 12" aria-hidden="true"><rect x="1" y="2.5" width="10" height="7"/><path d="M1 2.5l5 4 5-4"/></svg>
      </li>
      <li>www.ferncliffadvisory.com
        <svg viewBox="0 0 12 12" aria-hidden="true"><circle cx="6" cy="6" r="5"/><path d="M1 6h10M6 1c2 2.5 2 7.5 0 10M6 1c-2 2.5-2 7.5 0 10"/></svg>
      </li>
    </ul>
  </section>
</body>
</html>
```